Business card

I have changed logo's and colors. I have uploaded the new logo and colors.

In my head I am thinking about the main logo and text beside logo to be on one side of the card. The other side of the card to have just my picture and contact information.

The "R" emblem and the "equal housing" emblem... cut he MLS from the "R". and remove the wording from the house emblem.

Info on Card:

Lyle Penrose
Designated Broker, CDPE, CNE, GRI
Direct: 602.555.0143
Fax: 623.555.0187
Lyle@PenroseandAssociates.example
www.PenroseandAssociates.example
4153 West Marlow Lane Glendale, AZ 85391

Please see brief as I have uploaded a new logo and a few notes.

Reason: I changed the logo and colors. Please see brief

I am leaning towards maybe a black business card(or at least on the front where the logo is). I liked several designs that were submitted. Please re-submit.

```html
<!DOCTYPE html>
<html lang="en">
<head>
<meta charset="utf-8">
<title>Penrose &amp; Associates — Business Card</title>
<link href="https://fonts.googleapis.com/css2?family=Pinyon+Script&family=Questrial&display=swap" rel="stylesheet">
<style>
  :root {
    --ink: #1f1d1d;
    --paper: #ffffff;
    --accent: #e08a2e;
    --muted: #7d8a95;
    --rule: #8c8c8c;
    --stage: #e9e9e9;
    --photo-light: #f2f0ee;
    --photo-mid: #c9c3bd;
    --photo-dark: #3a3b40;
    --emblem: #d9d9d9;
  }
  * { box-sizing: border-box; margin: 0; padding: 0; }
  html, body { width: 1200px; height: 871px; overflow: hidden; }
  body {
    background: radial-gradient(ellipse at center, #f7f7f7 0%, var(--stage) 100%);
    font-family: "Questrial", "Helvetica Neue", Arial, sans-serif;
    position: relative;
  }
  .card {
    position: absolute;
    top: 103px;
    width: 380px;
    height: 665px;
    background: var(--ink);
    overflow: hidden;
    box-shadow: 0 14px 30px rgba(0,0,0,.22);
  }
  .card--brand { left: 170px; }
  .card--contact { left: 650px; }
  .card__shapes { position: absolute; inset: 0; width: 100%; height: 100%; }

  .brand { position: absolute; display: flex; align-items: center; gap: 14px; }
  .brand__dot { width: 54px; height: 54px; border-radius: 50%; flex: none; background: var(--muted); }
  .brand__name { line-height: 1.05; letter-spacing: 1px; text-transform: uppercase; color: var(--muted); font-size: 30px; }
  .brand--main { left: 40px; top: 62px; }

  .holder__name {
    position: absolute; left: 40px; top: 300px;
    font-family: "Pinyon Script", "Brush Script MT", cursive;
    font-weight: 400;
    font-size: 50px; color: var(--paper); line-height: 1;
  }
  .holder__rule {
    position: absolute; left: 36px; top: 368px; width: 300px; height: 1px;
    background: var(--paper);
  }
  .holder__title {
    position: absolute; left: 40px; top: 378px;
    font-size: 15px; color: var(--paper); letter-spacing: .3px;
  }
  .card__web {
    position: absolute; left: 0; right: 0; bottom: 48px; text-align: center;
    color: var(--accent); font-size: 17px; letter-spacing: .5px;
  }

  .contact { position: absolute; left: 30px; top: 322px; width: 320px; list-style: none; }
  .contact__item {
    display: flex; align-items: center; gap: 14px;
    color: var(--paper); font-size: 15px;
    padding: 11px 0 9px;
    border-bottom: 1px solid var(--rule);
  }
  .contact__item:last-child { border-bottom: none; }
  .contact__icon { width: 20px; height: 20px; flex: none; fill: var(--paper); }
  .contact__address { line-height: 1.35; }

  .emblems { position: absolute; right: 30px; bottom: 34px; display: flex; gap: 14px; }
  .emblem { width: 38px; height: 38px; background: var(--emblem); }
  .emblem--square { border-radius: 3px; }
  .emblem--round { border-radius: 50%; }
</style>
</head>
<body>

<section class="card card--brand" aria-label="Card side with company name">
  <svg class="card__shapes" viewBox="0 0 380 665" aria-hidden="true">
    <rect width="380" height="665" fill="var(--ink)"/>
    <path d="M0 0 H380 V180 C300 205 250 150 170 160 C100 168 50 200 0 205 Z" fill="var(--paper)"/>
    <path d="M0 205 C50 200 100 168 170 160 C250 150 300 205 380 180"
          fill="none" stroke="var(--accent)" stroke-width="4"/>
    <rect width="380" height="4" fill="var(--accent)"/>
  </svg>
  <div class="brand brand--main">
    <span class="brand__dot"></span>
    <span class="brand__name">Penrose &amp;<br>Associates</span>
  </div>
  <h1 class="holder__name">Lyle Penrose</h1>
  <div class="holder__rule"></div>
  <p class="holder__title">Designated Broker, CDPE, CNE, GRI</p>
  <p class="card__web">www.PenroseandAssociates.example</p>
</section>

<section class="card card--contact" aria-label="Card side with portrait and contact details">
  <svg class="card__shapes" viewBox="0 0 380 665">
    <defs>
      <linearGradient id="portraitTone" x1="0" y1="0" x2="0" y2="1">
        <stop offset="0" stop-color="var(--photo-light)"/>
        <stop offset=".55" stop-color="var(--photo-mid)"/>
        <stop offset="1" stop-color="var(--photo-dark)"/>
      </linearGradient>
    </defs>
    <rect width="380" height="665" fill="var(--ink)"/>
    <path role="img" aria-label="Portrait photo of Lyle Penrose in a dark suit"
          d="M0 0 H380 V215 C290 205 230 285 120 300 C70 306 30 300 0 292 Z"
          fill="url(#portraitTone)"/>
    <path d="M0 292 C30 300 70 306 120 300 C230 285 290 205 380 215"
          fill="none" stroke="var(--accent)" stroke-width="4"/>
    <rect width="380" height="4" fill="var(--accent)"/>
  </svg>
  <ul class="contact">
    <li class="contact__item">
      <svg class="contact__icon" viewBox="0 0 24 24"><path d="M6.6 10.8a15.2 15.2 0 0 0 6.6 6.6l2.2-2.2a1 1 0 0 1 1-.25 11.4 11.4 0 0 0 3.6.57 1 1 0 0 1 1 1V20a1 1 0 0 1-1 1A17 17 0 0 1 3 4a1 1 0 0 1 1-1h3.5a1 1 0 0 1 1 1c0 1.250.2 2.450.57 3.57a1 1 0 0 1-.25 1z"/></svg>
      <span>602.555.0143</span>
    </li>
    <li class="contact__item">
      <svg class="contact__icon" viewBox="0 0 24 24"><path d="M7 3h8l2 2v4h2a2 2 0 0 1 2 2v8a2 2 0 0 1-2 2H5a2 2 0 0 1-2-2v-8a2 2 0 0 1 2-2h2zm2 2v4h6V6h-1V5zm-3 7v2h4v-2zm0 4v2h4v-2zm8-4v2h2v-2zm0 4v2h2v-2z"/></svg>
      <span>623.555.0187</span>
    </li>
    <li class="contact__item">
      <svg class="contact__icon" viewBox="0 0 24 24"><path d="M3 5h18a1 1 0 0 1 1 1v12a1 1 0 0 1-1 1H3a1 1 0 0 1-1-1V6a1 1 0 0 1 1-1zm1 2.3V17h16V7.3l-8 5.2z"/></svg>
      <span>Lyle@PenroseandAssociates.example</span>
    </li>
    <li class="contact__item">
      <svg class="contact__icon" viewBox="0 0 24 24"><path d="M12 2a7 7 0 0 1 7 7c0 5-7 13-7 13S5 14 5 9a7 7 0 0 1 7-7zm0 4.5A2.5 2.5 0 1 0 12 11.5 2.5 2.5 0 0 0 12 6.5z"/></svg>
      <span class="contact__address">4153 West Marlow Lane<br>Glendale, AZ 85391</span>
    </li>
  </ul>
  <div class="emblems">
    <span class="emblem emblem--square" role="img" aria-label="Trade association membership badge"></span>
    <span class="emblem emblem--round" role="img" aria-label="Fair housing badge"></span>
  </div>
</section>

</body>
</html>
```